Design Startseite Kanzlei-Homepage
Zielgruppe
Wir sind eine Rechtsanwaltskanzlei in Kempten (Allgäu) und regional sowie überregional in verschiedenen Rechtsgebieten tätig. Unsere Zielgruppe sind sowohl private als auch gewerbliche Mandanten.
Aufgabenstellung
Die bestehende Gestaltung wirkt derzeit aus unserer Sicht überholt. Insbesondere soll das bislang dominierende Rot vollständig entfallen.
Stattdessen stellen wir uns ein modernes, hochwertiges Erscheinungsbild vor, primär in dunklen Farbtönen (Anthrazit/Schwarz) kombiniert mit Beige- bzw. warmen Naturtönen. Ziel ist eine klare visuelle Anlehnung an unsere Kanzleiräumlichkeiten (siehe Fotos).
Die Webseite soll insgesamt moderner, klarer und visuell anspruchsvoller wirken, ohne an Seriosität und Zugänglichkeit einzubüßen. Die Balance zwischen hochwertigem Erscheinungsbild und mandantenorientierter Nutzerführung steht für uns im Vordergrund.

```html
<!DOCTYPE html>
<html lang="de">
<head>
<meta charset="utf-8">
<title>Kanzlei Lindenhof – Startseite</title>
<link rel="stylesheet" href="https://fonts.googleapis.com/css2?family=Open+Sans:wght@400;600;700&family=Playfair+Display:wght@400&display=swap">
<style>
:root{
  --ink:#1f1f1f;
  --band:#262626;
  --dark:#202020;
  --paper:#f3f2f0;
  --card:#f8f7f5;
  --gold:#cfae88;
  --gold-line:#c9a37a;
  --text:#2c2c2c;
  --muted:#6b6b6b;
  --light:#e9e6e1;
}
*{margin:0;padding:0;box-sizing:border-box}
html,body{width:1200px;height:3144px;overflow:hidden}
body{font-family:"Open Sans",Arial,sans-serif;color:var(--text);background:var(--paper);position:relative}
.section{position:absolute;left:0;width:1200px}
.serif{font-family:"Playfair Display",Georgia,serif;font-weight:400}
.eyebrow{font-size:13px;font-weight:600;letter-spacing:.6px;color:#8a8a8a;text-transform:uppercase}
.rule{width:65px;height:2px;background:var(--gold-line)}
.btn{position:absolute;display:flex;align-items:center;justify-content:center;font-size:13px;font-weight:600;border-radius:2px}
.btn-gold{background:var(--gold);color:#1f1f1f}
.btn-ghost-light{border:1.5px solid #fff;color:#fff}
.btn-ghost-dark{border:1.5px solid #c9b39a;color:#2c2c2c;background:#faf9f7}

/* hero */
.hero{top:0;height:675px;background:linear-gradient(90deg,#141414 0%,#1c1c1c 35%,#3a342e 60%,#2a2622 100%);color:#fff}
.hero-photo{position:absolute;left:470px;top:0;width:730px;height:675px;background:radial-gradient(ellipse at 55% 45%,#8c7b66 0%,#4a4036 40%,#1e1c1a 80%)}
.hero-shade{position:absolute;left:0;top:0;width:760px;height:675px;background:linear-gradient(90deg,#151515 55%,rgba(21,21,21,0))}
.logo{position:absolute;font-weight:700;letter-spacing:.5px;display:flex;align-items:center;gap:8px}
.logo i{display:block;width:10px;height:10px;border:1.5px solid currentColor}
.hero .logo{left:51px;top:52px;font-size:25px}
.nav{position:absolute;left:411px;top:62px;display:flex;gap:34px;font-size:13.5px}
.nav-cta{left:999px;top:50px;width:150px;height:40px}
.hero h1{position:absolute;left:49px;top:222px;font-size:45px;line-height:59px}
.hero p{position:absolute;left:53px;top:370px;width:400px;font-size:12px;line-height:18px;color:#ddd}
.hero .b1{left:53px;top:472px;width:150px;height:39px}
.hero .b2{left:222px;top:472px;width:151px;height:39px}

/* features */
.features{top:675px;height:153px;background:var(--band);color:#fff}
.feature{position:absolute;top:56px;display:flex;gap:10px;align-items:center}
.feature .ic{width:40px;height:40px;border-radius:50%;background:#3a3936;display:flex;align-items:center;justify-content:center}
.feature b{display:block;font-size:12.5px;font-weight:700;margin-bottom:6px}
.feature span{font-size:12.5px;color:#ddd}

/* practice areas */
.areas{top:828px;height:644px;background:var(--paper)}
.areas .eyebrow{position:absolute;left:52px;top:83px}
.areas h2{position:absolute;left:49px;top:107px;font-size:34px;line-height:46px}
.areas .rule{position:absolute;left:51px;top:277px}
.areas .btn{left:50px;top:331px;width:211px;height:41px}
.area-card{position:absolute;width:281px;height:244px;background:var(--card);box-shadow:0 1px 4px rgba(0,0,0,.12);padding:30px 20px}
.area-card h3{font-size:16.5px;font-weight:700;margin:18px 0 22px}
.area-card p{font-size:12.5px;line-height:20px;color:#444}

/* reviews */
.reviews{top:1472px;height:264px;background:linear-gradient(90deg,#262626,#1d1e20 60%,#262626)}
.reviews .eyebrow{position:absolute;left:71px;top:53px;font-size:10.5px;color:#b99a78}
.reviews h2{position:absolute;left:71px;top:74px;font-size:24px;line-height:30px;color:#eee}
.review{position:absolute;top:43px;width:188px;height:170px;border:1px solid #3a3a3a;border-radius:3px;background:#242527;padding:14px 15px;color:#ddd}
.stars{color:#e2a83a;font-size:14px;letter-spacing:2px}
.review .q{position:absolute;right:13px;top:8px;font-family:"Playfair Display",serif;font-size:30px;color:#555}
.review p{font-size:12.5px;line-height:20px;margin-top:10px;height:72px}
.review b{display:block;font-size:10.5px;margin-top:14px}
.review small{font-size:8.5px;color:#aaa}
.score{left:959px;width:170px;text-align:center;color:#fff}
.score .mark{width:36px;height:36px;border-radius:50%;background:#3d3d40;margin:4px auto 8px}
.score .val{font-size:15px;font-weight:600}
.score small{display:block;font-size:8.5px;color:#bbb;margin-top:5px}
.score a{display:block;font-size:9.5px;font-weight:700;margin-top:14px;color:#fff;text-decoration:none}

/* office */
.office{top:1736px;height:580px;background:var(--paper)}
.video{position:absolute;left:52px;top:82px;width:578px;height:360px;background:linear-gradient(180deg,#6a655f 0%,#4a3f33 45%,#1f1f1f 100%)}
.play{position:absolute;left:270px;top:160px;width:38px;height:38px;border-radius:50%;background:rgba(200,180,150,.85);display:flex;align-items:center;justify-content:center}
.office .eyebrow{position:absolute;left:703px;top:86px}
.office h2{position:absolute;left:701px;top:109px;font-size:34px;line-height:46px}
.office .rule{position:absolute;left:703px;top:262px}
.office p{position:absolute;left:702px;top:300px;width:400px;font-size:12.5px;line-height:21px}
.office .btn{left:702px;top:393px;width:211px;height:41px}

/* team */
.team{top:2298px;height:386px;background:var(--paper)}
.team .eyebrow{position:absolute;left:49px;top:31px}
.team h2{position:absolute;left:47px;top:55px;font-size:34px;line-height:46px}
.team .rule{position:absolute;left:49px;top:166px}
.team .btn{left:50px;top:220px;width:211px;height:41px}
.member{position:absolute;top:0;width:197px;height:273px;background:#fff;box-shadow:0 1px 4px rgba(0,0,0,.12)}
.member .photo{height:203px;background:linear-gradient(180deg,#f2f2f2 0%,#c9c4be 60%,#3a3f4a 100%);position:relative}
.member .tag{position:absolute;right:0;bottom:0;background:var(--gold);color:#fff;font-size:8px;padding:2px 6px}
.member b{display:block;font-size:12.5px;font-weight:700;margin:12px 10px 8px}
.member span{font-size:12.5px;margin-left:10px;white-space:nowrap}
.member.fade{opacity:.35;overflow:hidden;width:150px}

/* cta */
.cta{top:2684px;height:264px;background:linear-gradient(90deg,#2a2826,#1a1a1a 50%,#2a2826);text-align:center;color:#fff}
.cta h2{position:absolute;left:0;width:1200px;top:56px;font-size:33px}
.cta p{position:absolute;left:0;width:1200px;top:111px;font-size:16px}
.cta .b1{left:440px;top:167px;width:150px;height:39px;font-size:13.5px}
.cta .b2{left:609px;top:167px;width:151px;height:39px;font-size:13.5px}

/* footer */
.footer{top:2948px;height:196px;background:var(--dark);color:#cfcfcf;border-top:1px solid #333}
.footer .logo{left:71px;top:26px;font-size:21px;color:#fff}
.footer .about{position:absolute;left:71px;top:70px;width:220px;font-size:10px;line-height:13px;color:#bbb}
.social{position:absolute;left:74px;top:152px;display:flex;gap:18px}
.social i{width:15px;height:15px;border-radius:50%;border:1.5px solid #999;display:block}
.vline{position:absolute;top:28px;width:1px;height:140px;background:#3a3a3a}
.col{position:absolute;top:28px;font-size:10px;line-height:18px;color:#bbb}
.col h4{font-size:10.5px;font-weight:700;color:#fff;letter-spacing:.5px;margin-bottom:6px}
</style>
</head>
<body>

<header class="section hero">
  <div class="hero-photo" role="img" aria-label="Abendaufnahme des beleuchteten Kanzleigebäudes an einer Straßenkreuzung"></div>
  <div class="hero-shade"></div>
  <div class="logo"><i></i>KANZLEI LINDENHOF</div>
  <nav class="nav"><span>Startseite</span><span>Rechtsgebiete</span><span>Kanzlei</span><span>Anwälte</span><span>Mandanten</span><span>Kontakt</span></nav>
  <div class="btn btn-gold nav-cta">Termin vereinbaren</div>
  <h1 class="serif">Kompetente Rechtsberatung<br>auf höchstem Niveau.</h1>
  <p>Wir begleiten Sie zuverlässig in allen rechtlichen Fragen – persönlich, engagiert und lösungsorientiert. Für Privatpersonen und Unternehmen – regional in Kempten und darüber hinaus.</p>
  <div class="btn btn-gold b1">Termin vereinbaren</div>
  <div class="btn btn-ghost-light b2">Jetzt Anfrage stellen</div>
</header>

<section class="section features">
  <div class="feature" style="left:51px"><div class="ic"><svg width="20" height="20"><circle cx="10" cy="10" r="8" fill="none" stroke="#cfae88" stroke-width="1.3"/><circle cx="10" cy="10" r="3" fill="none" stroke="#cfae88" stroke-width="1.3"/></svg></div><div><b>Persönlich &amp; individuell</b><span>Maßgeschneiderte Lösungen</span></div></div>
  <div class="feature" style="left:327px"><div class="ic"><svg width="20" height="20"><circle cx="10" cy="10" r="8" fill="none" stroke="#cfae88" stroke-width="1.3"/><circle cx="10" cy="10" r="3" fill="none" stroke="#cfae88" stroke-width="1.3"/></svg></div><div><b>Erfahren &amp; kompetent</b><span>Langjährige Praxiserfahrung</span></div></div>
  <div class="feature" style="left:602px"><div class="ic"><svg width="20" height="20"><circle cx="10" cy="10" r="8" fill="none" stroke="#cfae88" stroke-width="1.3"/><circle cx="10" cy="10" r="3" fill="none" stroke="#cfae88" stroke-width="1.3"/></svg></div><div><b>Vertrauensvoll &amp; diskret</b><span>Ihre Anliegen in sicheren Händen</span></div></div>
  <div class="feature" style="left:877px"><div class="ic"><svg width="20" height="20"><circle cx="10" cy="10" r="8" fill="none" stroke="#cfae88" stroke-width="1.3"/><circle cx="10" cy="10" r="3" fill="none" stroke="#cfae88" stroke-width="1.3"/></svg></div><div><b>Regional &amp; überregional</b><span>Für Sie in Kempten und darüber hinaus</span></div></div>
</section>

<section class="section areas">
  <div class="eyebrow">Unsere Rechtsgebiete</div>
  <h2 class="serif">Wir bieten umfassende<br>Rechtsberatung in<br>verschiedenen Bereichen.</h2>
  <div class="rule"></div>
  <div class="btn btn-ghost-dark">Alle Rechtsgebiete entdecken</div>

  <div class="area-card" style="left:514px;top:65px"><svg width="56" height="62" fill="none" stroke="#c9a37a" stroke-width="1.5"><rect x="2" y="4" width="40" height="52" rx="2"/><rect x="7" y="1" width="40" height="52" rx="2"/><rect x="17" y="14" width="20" height="13" rx="2"/><path d="M12 35h22M12 41h18M12 47h14M34 50l14-10M46 36l6 8"/></svg><h3>Arbeitsrecht</h3><p>Beratung und Vertretung bei Kündigungen, Verträgen und arbeitsrechtlichen Konflikten.</p></div>
  <div class="area-card" style="left:830px;top:65px"><svg width="56" height="62" fill="none" stroke="#c9a37a" stroke-width="1.5"><rect x="2" y="4" width="40" height="52" rx="2"/><rect x="7" y="1" width="40" height="52" rx="2"/><rect x="17" y="14" width="20" height="13" rx="2"/><path d="M12 35h22M12 41h18M12 47h14M34 50l14-10M46 36l6 8"/></svg><h3>Arbeitsrecht</h3><p>Beratung und Vertretung bei Kündigungen, Verträgen und arbeitsrechtlichen Konflikten.</p></div>
  <div class="area-card" style="left:514px;top:343px"><svg width="56" height="62" fill="none" stroke="#c9a37a" stroke-width="1.5"><rect x="2" y="4" width="40" height="52" rx="2"/><rect x="7" y="1" width="40" height="52" rx="2"/><rect x="17" y="14" width="20" height="13" rx="2"/><path d="M12 35h22M12 41h18M12 47h14M34 50l14-10M46 36l6 8"/></svg><h3>Arbeitsrecht</h3><p>Beratung und Vertretung bei Kündigungen, Verträgen und arbeitsrechtlichen Konflikten.</p></div>
  <div class="area-card" style="left:830px;top:343px"><svg width="56" height="62" fill="none" stroke="#c9a37a" stroke-width="1.5"><rect x="2" y="4" width="40" height="52" rx="2"/><rect x="7" y="1" width="40" height="52" rx="2"/><rect x="17" y="14" width="20" height="13" rx="2"/><path d="M12 35h22M12 41h18M12 47h14M34 50l14-10M46 36l6 8"/></svg><h3>Arbeitsrecht</h3><p>Beratung und Vertretung bei Kündigungen, Verträgen und arbeitsrechtlichen Konflikten.</p></div>
</section>

<section class="section reviews">
  <div class="eyebrow">Das sagen unsere Mandanten</div>
  <h2 class="serif">Vertrauen, das<br>unsere Mandanten<br>uns schenken.</h2>
  <div class="review" style="left:356px"><div class="stars">★★★★★</div><div class="q">”</div><p>Kompetente Beratung und schnelle Hilfe – absolut empfehlenswert.</p><b>Stefan K.</b><small>Online-Bewertung</small></div>
  <div class="review" style="left:557px"><div class="stars">★★★★★</div><div class="q">”</div><p>Sehr professionelle Kanzlei mit persönlichem Engagement.</p><b>Petra W.</b><small>Online-Bewertung</small></div>
  <div class="review" style="left:758px"><div class="stars">★★★★★</div><div class="q">”</div><p>Ich habe mich jederzeit bestens betreut gefühlt.</p><b>Daniel H.</b><small>Online-Bewertung</small></div>
  <div class="review score"><div class="mark"></div><div class="val">4,9 / 5</div><div class="stars">★★★★★</div><small>basierend auf 78 Bewertungen</small><a>Alle Bewertungen ansehen →</a></div>
</section>

<section class="section office">
  <div class="video" role="img" aria-label="Video: Wartebereich der Kanzlei mit Sitzbank, Holzwand und großem Bergpanorama"><div class="play"><svg width="14" height="16"><path d="M2 1l11 7-11 7z" fill="#fff"/></svg></div></div>
  <div class="eyebrow">Ein Einblick in unsere Kanzlei</div>
  <h2 class="serif">Lernen Sie unsere<br>Arbeitsweise und unsere<br>Kanzlei kennen.</h2>
  <div class="rule"></div>
  <p>Transparenz, moderne Strukturen und eine mandantenorientierte Arbeitsweise – das ist unser Anspruch.</p>
  <div class="btn btn-ghost-dark">Alle Rechtsgebiete entdecken</div>
</section>

<section class="section team">
  <div class="eyebrow">Ihre Ansprechpartner</div>
  <h2 class="serif">Unser erfahrenes<br>Anwaltsteam</h2>
  <div class="rule"></div>
  <div class="btn btn-ghost-dark">Alle Anwälte kennenlernen</div>
  <div class="member" style="left:361px"><div class="photo" role="img" aria-label="Porträtfoto eines Anwalts im Anzug"><span class="tag">Rechtsanwalt</span></div><b>Jonas Brenner</b><span>Fachanwalt für Familienrecht</span></div>
  <div class="member" style="left:573px"><div class="photo" role="img" aria-label="Porträtfoto eines Anwalts im Anzug"><span class="tag">Rechtsanwalt</span></div><b>Jonas Brenner</b><span>Fachanwalt für Familienrecht</span></div>
  <div class="member" style="left:785px"><div class="photo" role="img" aria-label="Porträtfoto eines Anwalts im Anzug"><span class="tag">Rechtsanwalt</span></div><b>Jonas Brenner</b><span>Fachanwalt für Familienrecht</span></div>
  <div class="member fade" style="left:998px"><div class="photo" role="img" aria-label="Porträtfoto eines Anwalts im Anzug"></div><b>Jonas Brenner</b><span>Fachanwalt für Familienrecht</span></div>
</section>

<section class="section cta" role="img" aria-label="Abgedunkelter Hintergrund mit Blick in die Kanzleiräume">
  <h2 class="serif">Benötigen Sie rechtliche Unterstützung?</h2>
  <p>Kontaktieren Sie uns für eine unverbindliche Erstanfrage – wir sind gerne für Sie da.</p>
  <div class="btn btn-gold b1">Termin vereinbaren</div>
  <div class="btn btn-ghost-light b2">Kontakt aufnehmen</div>
</section>

<footer class="section footer">
  <div class="logo"><i></i>KANZLEI LINDENHOF</div>
  <p class="about">Ihre Rechtsanwaltskanzlei in Kempten (Allgäu) – kompetent, engagiert und diskret. Regional verwurzelt, überregional tätig.</p>
  <div class="social"><i></i><i></i><i></i></div>
  <div class="vline" style="left:330px"></div>
  <div class="col" style="left:357px"><h4>KANZLEI</h4>Über uns<br>Anwälte<br>Philosophie<br>Karriere</div>
  <div class="vline" style="left:500px"></div>
  <div class="col" style="left:527px"><h4>RECHTSGEBIETE</h4>Arbeitsrecht<br>Familienrecht<br>Vertragsrecht<br>Weitere Rechtsgebiete</div>
  <div class="vline" style="left:688px"></div>
  <div class="col" style="left:715px"><h4>SERVICE</h4>Mandanteninformationen<br>Downloads<br>FAQ<br>Kontakt</div>
  <div class="vline" style="left:882px"></div>
  <div class="col" style="left:909px;line-height:14px"><h4>KONTAKT</h4>Kanzlei Lindenhof<br>Lindenweg 12<br>87435 Kempten (Allgäu)<br><br>+49 (0) 831 5 40 19 - 0<br>info@kanzlei-lindenhof.de<br><br>Öffnungszeiten:<br>Mo – Fr: 08:00 – 17:00 Uhr</div>
</footer>

</body>
</html>
```